Business Card for my New Brokerage

Looking to get a business card design for my new Real Estate Brokerage.
I want it with Picture, Phone Number, Email, Website, Office Address
Name and Designation. Please add logo too.

Target Market(s)

Real Estate Investors or Home Buyers

Industry/Entity Type

Real Estate

Contact Information for Business Card

Name, Email, Phone Number, website, email, office address

Colors
EB3D1F
EC4F4E
F09395
F8D3D4
FCEDEE

Requirements
Must have
• Minimalistic, Clean, Modern, Photo
Nice to have
• White and Red Colors

```html
<!DOCTYPE html>
<html lang="en">
<head>
<meta charset="utf-8">
<title>Ember Realty Inc – Business Card</title>
<link rel="stylesheet" href="https://fonts.googleapis.com/css2?family=Montserrat:wght@400;500;700;800&display=swap">
<style>
  :root {
    --red: #d90000;
    --red-deep: #b80000;
    --gold: #d6b25e;
    --white: #ffffff;
    --ink: #3a3a3a;
    --stage: #1c1c1e;
    --photo-light: #e9edf3;
    --photo-dark: #2a3550;
  }
  * { box-sizing: border-box; margin: 0; padding: 0; }
  html, body { width: 1200px; height: 900px; overflow: hidden; }
  body {
    background: var(--stage);
    font-family: "Montserrat", sans-serif;
    display: flex;
    flex-direction: column;
    align-items: center;
    justify-content: space-evenly;
  }
  .card {
    position: relative;
    width: 630px;
    height: 360px;
    border-radius: 22px;
    overflow: hidden;
  }

  /* Front */
  .card-front { background: var(--white); }
  .brand-logo {
    position: absolute;
    left: 92px;
    top: 26px;
    color: var(--red);
    font-weight: 800;
    line-height: 1;
  }
  .brand-logo .brand-main { font-size: 50px; letter-spacing: 1px; display: block; }
  .brand-logo .brand-sub { font-size: 15px; letter-spacing: 6px; display: block; margin-top: 4px; padding-left: 12px; }
  .name-accent {
    position: absolute;
    left: 0; top: 120px;
    width: 56px; height: 22px;
    background: var(--red);
  }
  .contact-block { position: absolute; left: 70px; top: 118px; color: var(--ink); z-index: 2; }
  .person-name { color: var(--red); font-weight: 800; font-size: 23px; letter-spacing: .5px; }
  .person-title { font-size: 14px; margin: 4px 0 10px; }
  .address-line { font-size: 13.5px; line-height: 1.35; }
  .contact-list { list-style: none; margin-top: 6px; }
  .contact-list li { display: flex; align-items: center; gap: 8px; font-size: 13.5px; line-height: 1.5; }
  .contact-list svg { width: 11px; height: 11px; flex: none; }

  .portrait {
    position: absolute;
    right: 30px; bottom: 0;
    width: 290px; height: 270px;
    border-radius: 140px 140px 0 0;
    background: linear-gradient(180deg, var(--photo-light) 0%, #c9b29c 45%, var(--photo-dark) 75%);
  }
  .swoosh { position: absolute; left: 0; bottom: 0; width: 630px; height: 64px; }

  /* Back */
  .card-back {
    background: var(--red);
    display: flex;
    align-items: center;
    justify-content: center;
  }
  .card-back .brand-logo {
    position: static;
    color: var(--white);
    text-align: center;
  }
  .card-back .brand-main { font-size: 92px; letter-spacing: 3px; }
  .card-back .brand-sub { font-size: 24px; letter-spacing: 12px; padding-left: 0; margin-top: 8px; }
</style>
</head>
<body>

  <section class="card card-front">
    <div class="brand-logo">
      <span class="brand-main">EMBER</span>
      <span class="brand-sub">REALTY INC</span>
    </div>
    <div class="name-accent"></div>
    <div class="contact-block">
      <h1 class="person-name">DANIEL HALE</h1>
      <p class="person-title">Founder and President</p>
      <p class="address-line">2180 Birchwood Court</p>
      <p class="address-line">Maple Ridge, GA 30412</p>
      <ul class="contact-list">
        <li>
          <svg viewBox="0 0 12 12"><path d="M2 1h3l1 3-2 1a7 7 0 0 0 3 3l1-2 3 1v3c-6 1-10-3-9-9z" fill="#d90000"/></svg>
          +330 2481-5570
        </li>
        <li>
          <svg viewBox="0 0 12 12"><rect x="1" y="2.5" width="10" height="7" fill="none" stroke="#d90000" stroke-width="1.3"/><path d="M1 3l5 3.5L11 3" fill="none" stroke="#d90000" stroke-width="1.3"/></svg>
          info@emberrealtyinc.com
        </li>
        <li>
          <svg viewBox="0 0 12 12"><circle cx="6" cy="6" r="5" fill="none" stroke="#d90000" stroke-width="1.3"/><path d="M1 6h10M6 1c-3 3-3 7 0 10M6 1c3 3 3 7 0 10" fill="none" stroke="#d90000" stroke-width="1"/></svg>
          www.emberrealtyinc.com
        </li>
      </ul>
    </div>
    <div class="portrait" role="img" aria-label="Portrait photo of the founder in a navy blazer and light blue shirt"></div>
    <svg class="swoosh" viewBox="0 0 630 64" preserveAspectRatio="none" aria-hidden="true">
      <path d="M0 26 C160 38 300 50 420 64 L0 64 Z" fill="var(--red)"/>
      <path d="M0 20 C170 32 320 48 440 64" fill="none" stroke="var(--gold)" stroke-width="4"/>
    </svg>
  </section>

  <section class="card card-back">
    <div class="brand-logo">
      <span class="brand-main">EMBER</span>
      <span class="brand-sub">REALTY INC</span>
    </div>
  </section>

</body>
</html>
```